www.lanternmerow.net

Hi,
UPDATE: Logo attached
TAG LINE NEW: OBITUARIES * CONDOLENCE NOTES
MULTIMEDIA MEMORIAL
Please refer to our existing site for more explanation of who we are?
We are a global data collecting portal site managing the Jewish funeral industry where users:
a) family and freinds in grief or "ancestry" searching persons
b) chevra kadisha's (funeral parlor)
c) current and historic cemetaries
d) Jewish Media Partners
arrive and choose a function (category):
in order to:
- upload a basic listing (FREE)
- upload/upgrade a multimedia listing (PAID)
- or search for a listing
of a deceased person (potentially millions of entries)
The functions (or categories) are accessed after the user:
Chooses their global location of search by
"Choose your Location" ie: Australia/NZ (which country?)
and allows the USER to choose a category function such as:
GROUP A (Local Info) GROUP B (Soul Search)
Chevra Kadisha Funerals (within 7 days)
Cemetaries Recently Deceased (up to 12mth)
Stonemasons Soul Search (after 1 year)
Jewish Media Partners
GROUP C (Jewish Death & Mourning Customs)
The way of Jewish burial
3000 y/old customs
When will Moshiach Come ?
Will I see my loved one again?
AIM:
To utilize existing logo and side menus (Member, Main & Resources) to create a user freindly and simpler friendly landing page, warmer and more softer for viewers.
To create logo buttons for the service catogories:
A, B & C and separate sub catagories
The MAIN AIM is to offer users opportunity to upload (LOG-IN required)
a) NEW basic FREE listing
b) NEW Multi-media PAID listing
SUMMARY:
1) User arrives at landing paid and sees global map, where he/she must choose the location in order to localize his data search
At this point, he/she can see what the site offers by the side MAIN, menu and icon function/catagories
(ie: Soul Search, New Basic Listing, Multimedia Listing)
2) After arriving at location (ie: Australia/NZ), the user then chooses the sub-function icon:
A- Local Funeral Service Info (Chevra Kadisha, Cemetary etc)
B- Soul Search (Funeral,Recently Deceased, Soul Search)
C- Jewish Death & Mourning Cutoms
Updates
Hi
Reason: Because of the holidays, we are happy to extend the deadline....
happy times
Target Market(s)
Family persons (Guest Member) & Industry (Members)
Industry/Entity Type
Industry
Requirements
Must have
- Style : Simple, Neat & Easy to Navigate
Icons: for each catagory/function
Colors; natural
-
Ability to bring inspiration, hope, light and healing to a difficult subject matter. (site look)
-
Education a profoundly deep 3000 y/old historically rich and mystic tradition to a wide audience
-
Allow children to access and upload data about grandparents etc
-
To promote on landing page the Invitation of local Chevra Kadisha's (funeral parlors), who have no web exposure, to get involved and LOG-IN and upload basic or multimedia listings.
(ie: please Register your local Chevra Kadisha here)
-
To promote on the landing page sample listings (Recently Deceased), to show look/feel of listings

```html
<!DOCTYPE html>
<html lang="en">
<head>
<meta charset="utf-8">
<title>LanternMerow.net – Global Memorial Network</title>
<link rel="stylesheet" href="https://fonts.googleapis.com/css2?family=Cardo&family=Open+Sans:wght@400;600&family=PT+Sans+Narrow&display=swap">
<style>
  :root {
    --orange: #f39a1f;
    --orange-deep: #d9700a;
    --orange-light: #fbbf5c;
    --ink: #222;
    --text: #333;
    --muted: #666;
    --panel: #e4e4e4;
    --panel-line: #c9c9c9;
    --dark: #3d3d3d;
    --nav-grey: #e9e9e9;
    --white: #fff;
    --heading: Cardo, "Times New Roman", serif;
    --body: "Open Sans", Arial, sans-serif;
  }
  * { box-sizing: border-box; margin: 0; padding: 0; }
  html, body { width: 1029px; height: 1200px; overflow: hidden; background: var(--white); }
  body { position: relative; font-family: var(--body); color: var(--text); }
  .abs { position: absolute; }

  /* Header */
  .brand { left: 54px; top: 62px; width: 170px; text-align: right; }
  .brand-name { font-family: var(--heading); font-size: 19px; color: var(--ink); display: flex; align-items: center; justify-content: flex-end; gap: 6px; }
  .brand-dot { width: 10px; height: 10px; border-radius: 50%; background: var(--orange); }
  .brand-region { font-size: 12px; color: var(--ink); margin-top: 30px; }
  .world-map { left: 237px; top: 0; width: 340px; height: 155px; background: radial-gradient(ellipse at center, #d6d6d6 0%, #ececec 60%, #fff 100%); }

  .region-picker { left: 540px; top: 0; width: 290px; height: 78px; background: var(--panel); border-radius: 0 0 6px 6px; padding: 9px 14px; }
  .picker-row { display: flex; align-items: center; height: 33px; }
  .picker-row label { width: 116px; font-size: 13px; color: var(--muted); }
  .select { width: 148px; height: 24px; border-radius: 12px; background: var(--white); border: 1px solid #ccc; font-size: 13px; color: var(--ink); padding: 2px 12px; position: relative; }
  .select::after { content: "▼"; position: absolute; right: 12px; top: 4px; font-size: 9px; }

  .login { left: 839px; top: 25px; width: 190px; height: 152px; background: var(--dark); border-radius: 6px 0 0 6px; padding: 17px 19px 0; }
  .login-tab { left: 925px; top: 0; width: 73px; height: 29px; background: var(--orange); color: var(--white); font-family: var(--heading); font-size: 19px; text-align: center; line-height: 28px; }
  .login-tab::after { content: ""; position: absolute; left: 29px; bottom: -6px; border: 6px solid transparent; border-top-color: var(--orange); border-bottom: 0; }
  .field { height: 26px; border-radius: 8px; background: var(--white); font-size: 12px; color: #888; padding: 5px 17px; margin-bottom: 7px; }
  .sign-in { display: block; width: 70px; margin: 11px auto 8px; height: 23px; border-radius: 6px; background: linear-gradient(var(--orange-light), var(--orange)); color: var(--white); font-family: var(--heading); font-size: 16px; text-align: center; line-height: 22px; }
  .login-note { font-size: 9.5px; color: var(--white); text-align: center; white-space: nowrap; }

  /* Navigation */
  .nav { left: 0; top: 166px; width: 1029px; height: 36px; background: linear-gradient(#f2f2f2, #dedede); }
  .nav a { position: absolute; top: 0; height: 36px; line-height: 34px; font-family: var(--heading); font-size: 18px; color: #555; text-decoration: none; }
  .nav .active { background: linear-gradient(var(--orange-light), var(--orange)); padding: 0 15px; color: #5a3a10; }
  .submenu { left: 218px; top: 202px; width: 148px; height: 184px; background: rgba(80,80,80,.88); z-index: 5; padding-top: 13px; }
  .submenu a { display: block; height: 31px; line-height: 27px; padding-left: 26px; font-size: 13px; color: var(--white); text-decoration: none; }
  .submenu .current { background: #3a3a3a; height: 23px; line-height: 23px; margin-bottom: 8px; }

  /* Slider */
  .slider-shadow { left: 14px; top: 225px; width: 1001px; height: 330px; border-radius: 50% / 10%; background: radial-gradient(ellipse at center, #fff 60%, #cfcfcf 100%); }
  .slide { left: 40px; top: 213px; width: 959px; height: 282px; border-radius: 6px 6px 0 0; background: linear-gradient(120deg, #e9ddd0 0%, #c98a3a 35%, #b06516 55%, #e7d7c6 80%, #d8c7b5 100%); }
  .slide-caption { left: 36px; top: 495px; width: 967px; height: 38px; background: var(--white); font-family: var(--heading); font-size: 23px; color: var(--ink); text-align: center; line-height: 38px; }
  .slide-arrow { top: 341px; width: 40px; height: 40px; border-radius: 5px; background: var(--orange-deep); }
  .slide-arrow svg { display: block; margin: 11px auto; }

  /* Partners */
  .partners { left: 50px; top: 556px; width: 938px; height: 46px; display: flex; align-items: center; }
  .partners .nudge { width: 0; height: 0; border: 9px solid transparent; }
  .partner { font-family: var(--heading); color: #333; font-size: 17px; white-space: nowrap; }

  /* Main copy */
  .intro { left: 56px; top: 652px; width: 618px; }
  .intro h1 { font-family: var(--heading); font-weight: 400; font-size: 23px; color: var(--ink); margin-bottom: 30px; }
  .region-map { float: left; width: 117px; height: 90px; margin: 4px 10px 0 0; background: #7a7a7a; border-radius: 30% 40% 45% 30%; }
  .intro p { font-size: 12.4px; line-height: 18.5px; color: #111; margin-bottom: 18px; }
  .read-more { display: inline-block; height: 24px; line-height: 24px; padding: 0 10px; border-radius: 6px; background: #ddd; color: #777; font-size: 12.5px; }
  .intro-more { left: 584px; top: 1093px; }

  /* Side panels */
  .panel { background: var(--panel); border: 1px solid var(--panel-line); border-radius: 5px; }
  .translate { left: 708px; top: 633px; width: 290px; height: 74px; background: #efefef; padding: 10px 15px; text-align: center; }
  .translate .select { width: 100%; height: 28px; border-radius: 4px; text-align: left; color: #888; padding-top: 5px; }
  .translate small { display: block; margin-top: 6px; font-size: 13px; color: var(--muted); }
  .translate strong { font-weight: 600; color: #4a6fb5; }

  .register { left: 710px; top: 722px; width: 291px; height: 199px; }
  .panel-title { position: absolute; left: 0; top: 0; height: 40px; border-radius: 5px 5px 0 0; background: linear-gradient(#c8c8c8, #fafafa); font-family: var(--heading); font-size: 21px; color: #666; text-align: center; line-height: 38px; }
  .register .panel-title { width: 100%; }
  .advisor { position: absolute; left: 8px; top: 59px; width: 58px; height: 83px; background: linear-gradient(#8a6a4a, #3f4650); border-radius: 40% 40% 8px 8px; }
  .register p { position: absolute; left: 75px; top: 62px; width: 212px; font-size: 12px; line-height: 18.5px; color: #111; }
  .cta { position: absolute; left: 37px; top: 155px; width: 214px; height: 35px; border: 1px solid #c26a10; border-radius: 4px; background: linear-gradient(var(--orange-light), var(--orange)); font-family: "PT Sans Narrow", Arial, sans-serif; font-size: 24px; color: #111; text-align: center; line-height: 33px; }

  .recent { left: 710px; top: 946px; width: 291px; height: 173px; }
  .recent .panel-title { left: 38px; top: -2px; width: 206px; }
  .pager { position: absolute; right: 14px; top: 27px; display: flex; gap: 3px; }
  .entry { position: absolute; left: 11px; width: 271px; height: 60px; border-bottom: 1px solid #fff; }
  .entry h3 { font-weight: 400; font-size: 14.5px; color: #222; }
  .entry p { font-size: 11px; line-height: 19px; color: #555; width: 190px; }
  .entry .photo { position: absolute; right: 12px; top: 3px; width: 57px; height: 48px; }
  .recent .more { position: absolute; right: 16px; bottom: 4px; font-size: 10.5px; color: #666; }

  /* Footer */
  .footer-rule { left: 0; top: 1146px; width: 1029px; height: 1px; background: #ddd; }
  .copyright { left: 6px; top: 1161px; font-size: 12px; color: #999; }
  .social { left: 816px; top: 1157px; display: flex; gap: 12px; }
  .social span { width: 22px; height: 22px; border-radius: 3px; }
</style>
</head>
<body>

<header>
  <div class="abs brand">
    <div class="brand-name"><span class="brand-dot"></span>LanternMerow.net</div>
    <div class="brand-region">Australia</div>
  </div>
  <div class="abs world-map" role="img" aria-label="Grey world map with Israel marked"></div>

  <form class="abs region-picker">
    <div class="picker-row"><label>Choose Region :</label><div class="select">Israel</div></div>
    <div class="picker-row"><label>Choose Country:</label><div class="select">Israel</div></div>
  </form>

  <div class="abs login">
    <div class="field">Username</div>
    <div class="field">Password</div>
    <span class="sign-in">Sign in</span>
    <p class="login-note">Please Register a Memorial Page Here</p>
  </div>
  <div class="abs login-tab">Login</div>
</header>

<nav class="abs nav">
  <a class="active" style="left:218px">Home</a>
  <a style="left:328px">Local Information</a>
  <a style="left:534px">Soul Search</a>
  <a style="left:673px">Jewish Customs</a>
</nav>
<div class="abs submenu">
  <a class="current">Our mission</a>
  <a>About Us</a>
  <a>Personal Media</a>
  <a>Contact Us</a>
  <a>On-line Forum</a>
</div>

<section>
  <div class="abs slider-shadow"></div>
  <div class="abs slide" role="img" aria-label="Golden Star of David resting on a page of Hebrew text"></div>
  <div class="abs slide-caption">Welcome to the global Chevra Kadisha network</div>
  <div class="abs slide-arrow" style="left:32px"><svg width="14" height="18" viewBox="0 0 14 18"><path d="M13 0v18L0 9z" fill="#fff"/></svg></div>
  <div class="abs slide-arrow" style="left:966px"><svg width="14" height="18" viewBox="0 0 14 18"><path d="M1 0v18l13-9z" fill="#fff"/></svg></div>
</section>

<div class="abs partners">
  <span class="nudge" style="border-right-color:#bbb;border-left:0"></span>
  <span class="partner" style="margin-left:30px">The Kehila Times</span>
  <span class="partner" style="margin-left:32px">Southern Star News</span>
  <span class="partner" style="margin-left:32px">The Weekly Herald</span>
  <span class="partner" style="margin-left:32px">RootsLedger</span>
  <span class="partner" style="margin-left:32px">The Harbour Courier</span>
  <span class="nudge" style="border-left-color:#bbb;border-right:0;margin-left:auto"></span>
</div>

<main class="abs intro">
  <h1>Choose Your Region</h1>
  <div class="region-map" role="img" aria-label="Grey silhouette map of Australia"></div>
  <p>Contrary to popular belief, Lorem Ipsum is not simply random text. It has roots in a piece of classical Latin literature from 45 BC, making it over 2000 years old. Edmund Harrow, a Latin professor at Larkfield College in Virginia, looked up one of the more obscure Latin words, consectetur, from a Lorem Ipsum passage, and going through the cites of the word in classical literature, discovered the undoubtable source. Lorem Ipsum comes from sections 1.10.32 and 1.10.33 of "de Finibus Bonorum et Malorum" (The Extremes of Good and Evil) by Tullan, written in 45 BC. This book is a treatise on the theory of ethics, very popular during the Renaissance. Contrary to popular belief, Lorem Ipsum is not simply random text. It has roots in a piece of classical Latin literature from 45 BC, making it over 2000 years old.</p>
  <p>Edmund Harrow, a Latin professor at Larkfield College in Virginia, looked up one of the more obscure Latin words, consectetur, from a Lorem Ipsum passage, and going through the cites of the word in classical literature, discovered the undoubtable source. Lorem Ipsum comes from sections 1.10.32 and 1.10.33 of "de Finibus Bonorum et Malorum" (The Extremes of Good and Evil) by Tullan, written in 45 BC. This book is a treatise on the theory of ethics, very popular during the Renaissance. Contrary to popular belief, Lorem Ipsum is not simply random text. It has roots in a piece of classical Latin literature from 45 BC, making it over 2000 years old. Edmund Harrow, a Latin professor at Larkfield College in Virginia, looked up one of the more obscure Latin words, consectetur, from a Lorem Ipsum passage, and going through the cites of the word in classical literature, discovered the undoubtable source.</p>
</main>
<span class="abs read-more intro-more">Read more...</span>

<aside>
  <div class="abs panel translate">
    <div class="select">Select Language</div>
    <small>Powered by <strong>Linguaframe</strong> Translate</small>
  </div>

  <div class="abs panel register">
    <div class="panel-title">Register or Update a listing</div>
    <div class="advisor" role="img" aria-label="Illustrated businessman in a suit"></div>
    <p>Lorem Ipsum is simply dummy text of the printing and typesetting industry. Lorem Ipsum has been the industry's standard dummy text ever</p>
    <div class="cta">REGISTER HERE</div>
  </div>

  <div class="abs panel recent">
    <div class="panel-title">Recent Passings</div>
    <div class="pager">
      <svg width="7" height="9"><path d="M7 0v9L0 4.5z" fill="#aaa"/></svg>
      <svg width="7" height="9"><path d="M0 0v9l7-4.5z" fill="#aaa"/></svg>
    </div>
    <div class="entry" style="top:40px">
      <h3>Aaron Feldmark</h3>
      <p>Lorem Ipsum is simply dummy text of the printing&nbsp; fhlsdhlek dfk</p>
      <div class="photo" role="img" aria-label="Footprints in sand" style="background:linear-gradient(#c9a86a,#8c7040)"></div>
    </div>
    <div class="entry" style="top:102px;border-bottom:0">
      <h3>Aaron Feldmark</h3>
      <p>Lorem Ipsum is simply dummy text of the printing&nbsp; fhlsdhlek dfk</p>
      <div class="photo" role="img" aria-label="Portrait photo of the deceased" style="background:linear-gradient(#cfd8dc,#a58a70)"></div>
    </div>
    <span class="more">Read more...</span>
  </div>
</aside>

<footer>
  <div class="abs footer-rule"></div>
  <p class="abs copyright">Copyright © 2011. www.lanternmerow.net</p>
  <div class="abs social">
    <span style="background:#3b5b98"></span>
    <span style="background:#4fb5e0"></span>
    <span style="background:#f08a1c"></span>
    <span style="background:#1e77b4"></span>
    <span style="background:#2a6aa8"></span>
  </div>
</footer>

</body>
</html>
```